I need a website designed. I am a mortgage loan officer and would like to have a website for me and my team where i can post resources, videos and blog information for my clients. A website like themorvaskteam.com .

The theme is - The Pelkins Team - Home Loan Group powered by Brightwell Home Loans -

Target Market(s)

B2B (Real Estate Agents)and B2C (Home buyers and refinancing)

Industry/Entity Type

Mortgage Lender

Coding

Coded - Design and coding required

Number of Pages Required

5+ page

Font styles to use
Serif
Sans Serif

Colors

Designer to choose colors to be used in the design.

Requirements
Must have
• Disclaimers: Licensed by the Bureau of Lending Affairs under the Pacific Credit Providers Act. Loans made or arranged pursuant to a Pacific Credit Providers Act License. Equal Housing Lender Brightwell Cannot Accept mortgage applications for properties located in New York via this site
• Mobile Friendly
Nice to have
• Main Links: Home, About Us(see team flyer), Mortgage 101, Contact Us (formzig form)

```html
<!DOCTYPE html>
<html lang="en">
<head>
<meta charset="utf-8">
<title>The Pelkins Team – Home Loan Group</title>
<link href="https://fonts.googleapis.com/css2?family=Barlow:wght@400;500;600;700&family=Barlow+Condensed:wght@600;700&display=swap" rel="stylesheet">
<style>
:root{
  --blue:#1f6fc5;
  --blue-dark:#175ba6;
  --heading-blue:#2a78c8;
  --ink:#1e2024;
  --muted:#8a8f96;
  --light:#f0f0f1;
  --footer:#1d232c;
  --footer-text:#c7ccd3;
  --white:#ffffff;
}
*{box-sizing:border-box;margin:0;padding:0}
html,body{width:1200px;height:3488px;overflow:hidden}
body{font-family:"Barlow",Arial,sans-serif;color:var(--ink);background:var(--white);position:relative}
a{color:inherit;text-decoration:none}

/* top bar */
.topbar{position:absolute;top:0;left:0;width:1200px;height:47px;background:var(--blue)}
.search{position:absolute;left:67px;top:10px;width:198px;height:27px;background:var(--white);border-radius:14px;display:flex;align-items:center;justify-content:space-between;padding:0 12px;font-size:12px;font-weight:700;color:var(--ink)}
.contact-strip{position:absolute;right:40px;top:0;height:47px;display:flex;align-items:center;gap:20px;color:var(--white);font-size:10.5px;font-weight:600;white-space:nowrap}
.contact-strip span{display:flex;align-items:center;gap:6px}

.nav{position:absolute;top:47px;left:0;width:1200px;height:74px;background:var(--white)}
.nav-link{position:absolute;top:28px;font-size:13px;font-weight:700;letter-spacing:.4px}
.nav-link.active{color:var(--blue)}
.brand{position:absolute;left:490px;top:10px;width:220px;height:101px;background:var(--white);display:flex;flex-direction:column;align-items:center;justify-content:center}
.brand-mark{width:20px;height:20px;background:var(--blue);margin-bottom:6px}
.brand-name{font-family:"Barlow Condensed",Arial,sans-serif;font-weight:700;font-size:30px;color:var(--blue);line-height:1;white-space:nowrap}
.brand-sub{font-family:"Barlow Condensed",Arial,sans-serif;font-weight:600;font-size:14px;color:var(--blue);line-height:1;letter-spacing:3px;white-space:nowrap;margin-top:3px}

/* hero */
.hero{position:absolute;top:121px;left:0;width:1200px;height:500px;background:linear-gradient(100deg,#5b6f4a 0%,#b89b86 25%,#e7c7b8 48%,#d8b39a 62%,#8f9f86 82%,#4e6240 100%)}
.hero-shade{position:absolute;inset:0;background:rgba(20,25,30,.18)}
.hero-title{position:absolute;top:160px;width:100%;text-align:center;color:var(--white);font-family:"Barlow Condensed",Arial,sans-serif;font-weight:700;line-height:1}
.hero-title .l1{font-size:90px;display:block;letter-spacing:1px}
.hero-title .l2{font-size:54px;display:block;margin-top:2px;letter-spacing:1px}
.btn-hero{position:absolute;left:497px;top:331px;width:206px;height:50px;background:rgba(110,110,110,.85);color:var(--white);font-size:13px;font-weight:700;display:flex;align-items:center;justify-content:center;letter-spacing:.5px}
.dots{position:absolute;top:459px;left:0;width:100%;display:flex;justify-content:center;gap:10px}
.dots i{width:8px;height:8px;border-radius:50%;background:rgba(255,255,255,.6)}
.dots i:first-child{background:var(--white)}

/* sections */
.section-title{text-align:center;font-family:"Barlow Condensed",Arial,sans-serif;font-weight:700;font-size:32px;color:var(--heading-blue);letter-spacing:.5px}
.section-title::after{content:"";display:block;width:52px;height:4px;background:#b5b8bd;margin:12px auto 0}

.about{position:absolute;top:621px;left:0;width:1200px;height:444px;background:linear-gradient(90deg,var(--blue-dark),var(--blue) 50%,#2a7bd0)}
.about .section-title{color:var(--white);padding-top:78px}
.about .section-title::after{background:rgba(255,255,255,.55)}
.about p{width:620px;margin:26px auto 0;text-align:center;color:var(--white);font-size:13px;line-height:1.55}
.about p + p{margin-top:18px}
.btn-outline{display:flex;align-items:center;justify-content:center;width:206px;height:52px;border:1.5px solid currentColor;font-size:13px;font-weight:700;letter-spacing:.5px}
.about .btn-outline{position:absolute;left:497px;top:319px;color:var(--white)}

.videos{position:absolute;top:1065px;left:0;width:1200px;height:570px}
.videos .section-title{padding-top:90px}
.card-row{position:absolute;left:67px;display:flex;gap:24px}
.video{width:340px}
.thumb{width:340px;height:242px;position:relative}
.play{position:absolute;left:50%;top:50%;width:58px;height:58px;margin:-29px 0 0 -29px;border-radius:50%;background:var(--blue);border:3px solid var(--white);display:flex;align-items:center;justify-content:center}
.video h3{margin-top:17px;text-align:center;font-size:13px;font-weight:700;letter-spacing:.3px}

.team{position:absolute;top:1635px;left:0;width:1200px;height:731px;background:var(--light)}
.team .section-title{padding-top:90px}
.member{position:absolute;display:flex;gap:20px}
.photo{width:191px;height:177px;background:linear-gradient(180deg,#d9dadc,#a9adb2)}
.member-info h3{font-family:"Barlow Condensed",Arial,sans-serif;font-size:21px;font-weight:700;margin-top:-2px}
.member-info .role{font-size:11px;font-weight:600;color:#555;margin-top:2px}
.member-info .rule{width:52px;height:1px;background:#aaa;margin:10px 0}
.member-info .details{font-size:10.5px;color:var(--muted);line-height:1.5}
.member-info .btn-outline{width:108px;height:30px;font-size:11px;margin-top:14px;color:var(--blue)}

.blog{position:absolute;top:2366px;left:0;width:1200px;height:739px}
.blog .section-title{padding-top:58px}
.post{width:340px}
.post .thumb{height:175px}
.post h3{margin-top:86px;font-size:13px;font-weight:700;line-height:1.45;letter-spacing:.2px}
.post p{margin-top:16px;font-size:11px;color:var(--muted);line-height:1.55}
.post .rule{width:68px;height:1px;background:#999;margin:24px 0 14px}
.post time{font-size:13px;font-weight:700;color:var(--blue)}
.blog .btn-outline{position:absolute;left:497px;top:639px;color:var(--ink);border-color:var(--blue)}

/* footer */
.footer{position:absolute;top:3105px;left:0;width:1200px;height:383px;background:var(--footer);color:var(--footer-text)}
.f-brand{position:absolute;left:98px;top:40px;width:190px;text-align:center}
.f-brand .brand-mark{margin:0 auto 6px}
.f-brand .name{font-family:"Barlow Condensed",Arial,sans-serif;font-size:24px;font-weight:700;color:var(--heading-blue);white-space:nowrap}
.f-badges{display:flex;align-items:center;justify-content:center;gap:14px;margin-top:30px}
.f-badges .badge{width:42px;height:42px;background:#d9dde2}
.f-badges .partner{font-size:16px;font-weight:600;color:#9fb4cf}
.f-col{position:absolute;top:38px}
.f-col h4{font-size:12px;font-weight:700;color:var(--heading-blue);letter-spacing:.5px;margin-bottom:20px}
.f-col li{list-style:none;font-size:11px;font-weight:600;color:var(--white);margin-bottom:9px}
.res{font-size:10.5px;line-height:1.45;color:#8f96a0;display:flex;gap:8px;width:340px;margin-bottom:14px}
.res time{display:block;color:var(--heading-blue);font-weight:700;margin-top:6px}
.res-arrows{position:absolute;right:0;top:0;display:flex;gap:10px;color:var(--white);font-size:12px}
.disclaimer{position:absolute;left:0;width:1200px;text-align:center}
.disclaimer h4{font-size:11px;font-weight:700;color:var(--heading-blue);letter-spacing:.5px}
.disclaimer p{width:1110px;margin:8px auto 0;font-size:12px;line-height:1.55;color:var(--footer-text)}
.copyright{position:absolute;left:0;width:1200px;border-top:1px solid #343b45;padding-top:10px;text-align:center;font-size:11px;color:var(--white);font-weight:600}
</style>
</head>
<body>

<header>
  <div class="topbar">
    <div class="search">SEARCH
      <svg width="13" height="13" viewBox="0 0 14 14"><circle cx="5.8" cy="5.8" r="4.3" fill="none" stroke="#1e2024" stroke-width="2"/><line x1="9" y1="9" x2="13" y2="13" stroke="#1e2024" stroke-width="2"/></svg>
    </div>
    <div class="contact-strip">
      <span><svg width="10" height="14" viewBox="0 0 10 14"><path d="M5 0a5 5 0 0 1 5 5c0 4-5 9-5 9S0 9 0 5a5 5 0 0 1 5-5z" fill="#fff"/><circle cx="5" cy="5" r="1.8" fill="#1f6fc5"/></svg>4820 LAKEMONT RD, SUITE 112, BROOKHAVEN FL 32901</span>
      <span><svg width="12" height="12" viewBox="0 0 24 24"><path d="M6.6 10.8a15 15 0 0 0 6.6 6.6l2.2-2.2a1 1 0 0 1 1-.25 11 11 0 0 0 3.6.6 1 1 0 0 1 1 1V20a1 1 0 0 1-1 1A17 17 0 0 1 3 4a1 1 0 0 1 1-1h3.5a1 1 0 0 1 1 1 11 11 0 0 0 .6 3.6 1 1 0 0 1-.25 1z" fill="#fff"/></svg>1-555-014-2290</span>
    </div>
  </div>
  <nav class="nav">
    <a class="nav-link active" style="left:242px">HOME</a>
    <a class="nav-link" style="left:333px">ABOUT US</a>
    <a class="nav-link" style="left:725px">MORTGAGE 101</a>
    <a class="nav-link" style="left:874px">CONTACT US</a>
  </nav>
  <div class="brand">
    <div class="brand-mark"></div>
    <div class="brand-name">THE PELKINS TEAM</div>
    <div class="brand-sub">HOME LOAN GROUP</div>
  </div>
</header>

<section class="hero">
  <div class="hero-bg" role="img" aria-label="Smiling woman holding house keys in front of a pastel-coloured family home" style="position:absolute;inset:0"></div>
  <div class="hero-shade"></div>
  <h1 class="hero-title"><span class="l1">THE PELKINS TEAM</span><span class="l2">HOME LOAN GROUP</span></h1>
  <a class="btn-hero">LEARN MORE</a>
  <div class="dots"><i></i><i></i><i></i><i></i></div>
</section>

<section class="about">
  <h2 class="section-title">ABOUT US</h2>
  <p>Qui dolorem ipsum quia dolor sit amet, consectetur, adipisci velit, sed quia non numquam eius modi tempora incidunt ut labore et dolore magnam aliquam quaerat voluptatem.</p>
  <p>Ut enim ad minima veniam, quis nostrum exercitationem ullam corporis suscipit laboriosam, nisi ut aliquid ex ea commodi qui dolorem ipsum quia dolor sit amet, consectetur, adipisci velit, sed quia non numquam eius modi tempora</p>
  <a class="btn-outline">READ MORE</a>
</section>

<section class="videos">
  <h2 class="section-title">VIDEOS</h2>
  <div class="card-row" style="top:210px">
    <article class="video">
      <div class="thumb" role="img" aria-label="Couple touring a bright home interior with an agent" style="background:linear-gradient(135deg,#efe9e1,#c9b7a2)"><span class="play"><svg width="18" height="20" viewBox="0 0 18 20"><path d="M2 1l15 9-15 9z" fill="#fff"/></svg></span></div>
      <h3>QUIA DOLOR SIT AMET, CONSECTETU</h3>
    </article>
    <article class="video">
      <div class="thumb" role="img" aria-label="Modern house with a wooden deck at dusk" style="background:linear-gradient(160deg,#6b7a88,#8a6a4f 60%,#4a3a2c)"><span class="play"><svg width="18" height="20" viewBox="0 0 18 20"><path d="M2 1l15 9-15 9z" fill="#fff"/></svg></span></div>
      <h3>OCCAECATI CUPIDITATE NON PROVIDENT</h3>
    </article>
    <article class="video">
      <div class="thumb" role="img" aria-label="Family relaxing on the porch of their new home" style="background:linear-gradient(150deg,#a9bfa0,#e2dccf 55%,#7f8f6e)"><span class="play"><svg width="18" height="20" viewBox="0 0 18 20"><path d="M2 1l15 9-15 9z" fill="#fff"/></svg></span></div>
      <h3>POSSIMUS, OMNIS VOLUPTAS ASSUMENDA</h3>
    </article>
  </div>
</section>

<section class="team">
  <h2 class="section-title">OUR TEAM</h2>
  <div class="member" style="left:67px;top:203px">
    <div class="photo" role="img" aria-label="Portrait of Ivan Pelkins"></div>
    <div class="member-info">
      <h3>IVAN PELKINS</h3>
      <div class="role">Producing Branch Manager</div>
      <div class="rule"></div>
      <div class="details">Brightwell Home Loans, Inc – NMLS 00000<br>Ivan.Pelkins@brightwellhomeloans.com<br>Office: (555) 014-2290<br>Fax: (555) 014-2291</div>
      <a class="btn-outline">VIEW MORE</a>
    </div>
  </div>
  <div class="member" style="left:612px;top:203px">
    <div class="photo" role="img" aria-label="Portrait of Marco Delane"></div>
    <div class="member-info">
      <h3>MARCO DELANE</h3>
      <div class="role">Loan Partner</div>
      <div class="rule"></div>
      <div class="details">Brightwell Home Loans, Inc – NMLS 00000<br>NMLS ID 100200<br>Marco.Delane@brightwellhomeloans.com<br>(555) 014-2290</div>
      <a class="btn-outline">VIEW MORE</a>
    </div>
  </div>
  <div class="member" style="left:67px;top:431px">
    <div class="photo" role="img" aria-label="Portrait of Tomas Reyvel"></div>
    <div class="member-info">
      <h3>TOMAS REYVEL</h3>
      <div class="role">Loan Processor</div>
      <div class="rule"></div>
      <div class="details">NMLS ID 100300<br>Tomas.Reyvel@brightwellhomeloans.com<br>(555) 014-2292</div>
      <a class="btn-outline">VIEW MORE</a>
    </div>
  </div>
  <div class="member" style="left:612px;top:431px">
    <div class="photo" role="img" aria-label="Portrait of Lena Hartwick"></div>
    <div class="member-info">
      <h3>LENA HARTWICK</h3>
      <div class="role">Closing Coordinator/Team Leader</div>
      <div class="rule"></div>
      <div class="details">NMLS 100400<br>Lena.Hartwick@brightwellhomeloans.com<br>(555) 014-2293</div>
      <a class="btn-outline">VIEW MORE</a>
    </div>
  </div>
</section>

<section class="blog">
  <h2 class="section-title">BLOG</h2>
  <div class="card-row" style="top:151px">
    <article class="post">
      <div class="thumb" role="img" aria-label="Couple reviewing mortgage paperwork at a table" style="background:linear-gradient(135deg,#d8cfc4,#8f7d6c)"></div>
      <h3>SED UT PERSPICIATIS UNDE OMNIS ISTE NATUS ERROR SIT VOLUPTATEM ACCUSANTIUM</h3>
      <p>At vero eos et accusamus et iusto odio dignissimos ducimus qui blanditiis praesentium voluptatum deleniti atque corrupti quos dolores et quas molestias excepturi sint occaecati</p>
      <div class="rule"></div>
      <time>FEBRUARY 12 2018</time>
    </article>
    <article class="post">
      <div class="thumb" role="img" aria-label="Loan officer meeting clients in a bright office" style="background:linear-gradient(135deg,#e6e8ea,#9aa3ad)"></div>
      <h3>UNDE OMNIS ISTE NATUS ERROR SIT VOLUPTATEM ACCUSANTIUM</h3>
      <p>At vero eos et accusamus et iusto odio dignissimos ducimus qui blanditiis praesentium voluptatum deleniti atque corrupti quos dolores et quas molestias excepturi sint occaecati</p>
      <div class="rule"></div>
      <time>FEBRUARY 10 2018</time>
    </article>
    <article class="post">
      <div class="thumb" role="img" aria-label="Couple signing documents with an advisor" style="background:linear-gradient(135deg,#efe6dc,#b39a82)"></div>
      <h3>PERSPICIATIS UNDE OMNIS ISTE NATUS ERROR SIT VOLUPTATEM ACCUSANTIUM</h3>
      <p>At vero eos et accusamus et iusto odio dignissimos ducimus qui blanditiis praesentium voluptatum deleniti atque corrupti quos dolores et quas molestias excepturi sint occaecati</p>
      <div class="rule"></div>
      <time>FEBRUARY 9 2018</time>
    </article>
  </div>
  <a class="btn-outline">VIEW MORE BLOG</a>
</section>

<footer class="footer">
  <div class="f-brand">
    <div class="brand-mark"></div>
    <div class="name">THE PELKINS TEAM</div>
    <div class="f-badges"><span class="badge"></span><span class="partner">Brightwell</span></div>
  </div>
  <div class="f-col" style="left:356px">
    <h4>QUICK LINKS</h4>
    <ul><li>HOME</li><li>ABOUT US</li><li>MORTGAGE 101</li><li>CONTACT US</li></ul>
  </div>
  <div class="f-col" style="left:579px">
    <h4>OTHER LINKS</h4>
    <ul><li>TERMS OF USE</li><li>PRIVACY POLICY</li><li>HELP</li><li>DISCLAIMER</li></ul>
  </div>
  <div class="f-col" style="left:795px;width:340px">
    <h4>RESOURCES</h4>
    <div class="res-arrows"><span>&#8249;</span><span>&#8250;</span></div>
    <div class="res"><span>&#8250;</span><div>At vero eos et accusamus et iusto odio dignissimos ducimus qui blanditiis praesentium voluptatum<time>FEBRUARY 12TH 2018</time></div></div>
    <div class="res"><span>&#8250;</span><div>Deleniti atque corrupti quos dolores et quas molestias excepturi sint occaecati<time>FEBRUARY 8TH 2018</time></div></div>
  </div>
  <div class="disclaimer" style="top:255px">
    <h4>DISCLAIMER</h4>
    <p>Licensed by the Bureau of Lending Affairs under the Pacific Credit Providers Act. Loans made or arranged pursuant to a Pacific Credit Providers Act License. Equal Housing Lender Brightwell Cannot Accept mortgage applications for properties located in New York via this site.</p>
  </div>
  <div class="copyright" style="top:343px">© 2018 COMPANY NAME | ALL RIGHTS RESERVED</div>
</footer>

</body>
</html>
```